Brimsett Gardening Fresh New Website

We are looking to create a simple fresh website for our landscaping business. The website should appeal to a 'high end' audience. We deal with a lot of Embassies and affluent clients who have extremely large gardens that are meticulously maintained. The site is about communicating our excellent landscaping and customer service skills and encouraging new clients to reach out and engage us to take care of their gardens.

The website is basically going to be our business card, it will have almost no functionality other than two 'contact us' forms, one for smaller clients and one for more detailed projects.

The website will not have a lot of written content and will have to show photos of beautifully landscaped gardens.

The main logo in black will influence the site, however, we are open to all suggestions.

We are expecting to have the following pages:
Home Page
Services
About Us
Contact Us
Showcase (photo gallery of our work)

We need someone who can code it to wordpress and be available for minor changes over a number of days. They will be simple tweaks.

```html
<!DOCTYPE html>
<html lang="en">
<head>
<meta charset="utf-8">
<title>Brimsett Gardening</title>
<link href="https://fonts.googleapis.com/css2?family=Montserrat:wght@500;600;700;800&family=Lato:wght@400;700&display=swap" rel="stylesheet">
<style>
:root{
  --yellow:#f7d12a;
  --yellow-deep:#f2c418;
  --ink:#111111;
  --text:#333333;
  --muted:#777777;
  --light:#f3f3f3;
  --footer:#121212;
  --grey-btn:#6b6b6b;
}
*{box-sizing:border-box;margin:0;padding:0}
html,body{width:1200px;height:4164px;overflow:hidden;background:#fff}
body{font-family:'Lato',sans-serif;color:var(--text);position:relative}
.abs{position:absolute}
.heading{font-family:'Montserrat',sans-serif;font-weight:700;color:var(--ink);text-transform:uppercase}
.section-title{position:absolute;left:0;width:1200px;text-align:center;font-size:34px}
.icon-circle{position:absolute;border-radius:50%;display:flex;align-items:center;justify-content:center}

/* header */
.topbar{left:0;top:0;width:1200px;height:108px;border-bottom:4px solid var(--yellow)}
.contact-label{font-family:'Montserrat',sans-serif;font-size:14px;font-weight:600;color:var(--yellow-deep)}
.contact-value{font-size:17px;color:var(--ink)}
.brand{position:absolute;left:0;width:1200px;top:36px;text-align:center;font-family:'Montserrat',sans-serif;font-weight:600;font-size:18px;letter-spacing:5px;color:var(--ink);text-transform:uppercase}
.navbar{left:0;top:112px;width:1200px;height:53px;background:var(--light)}
.nav-item{position:absolute;top:16px;font-size:15px;color:var(--ink)}
.nav-home{position:absolute;left:136px;top:-4px;width:64px;height:49px;background:var(--yellow);border-radius:0 0 12px 12px;display:flex;align-items:flex-end;justify-content:center;padding-bottom:12px;font-size:15px;color:var(--ink)}
.search{position:absolute;left:788px;top:8px;width:284px;height:35px;background:#fff;border-radius:18px;padding:10px 0 0 22px;font-size:14px;color:#555}

/* hero */
.hero{left:0;top:165px;width:1200px;height:583px;background:radial-gradient(ellipse at 30% 30%,#5e6e4a 0%,#34432a 40%,#1c2616 100%)}
.hero-shade{left:0;top:0;width:1200px;height:583px;background:linear-gradient(90deg,rgba(0,0,0,.45),rgba(0,0,0,.1) 60%,rgba(0,0,0,.25))}
.hero-kicker{left:107px;top:120px;font-family:'Montserrat',sans-serif;font-weight:700;font-size:25px;color:var(--yellow)}
.hero-title{left:105px;top:153px;font-family:'Montserrat',sans-serif;font-weight:700;font-size:62px;line-height:68px;color:#fff}
.hero-text{left:113px;top:304px;width:380px;font-size:16px;line-height:26px;color:#fff}
.btn-yellow{position:absolute;background:var(--yellow);border-radius:26px;font-family:'Montserrat',sans-serif;font-weight:700;color:var(--ink);display:flex;align-items:center;justify-content:center}

/* services */
.card{position:absolute;top:910px;width:316px;height:338px}
.card-img{position:absolute;inset:0}
.card-shade{position:absolute;inset:0;background:linear-gradient(180deg,rgba(0,0,0,0) 45%,rgba(0,0,0,.7))}
.card-title{position:absolute;left:22px;top:213px;font-family:'Montserrat',sans-serif;font-weight:600;font-size:23px;color:#fff}
.card-text{position:absolute;left:22px;top:256px;width:260px;font-size:16px;line-height:26px;color:#fff}
.card-arrow{position:absolute;right:10px;bottom:-24px;width:50px;height:50px;border-radius:50%;background:var(--yellow);border:4px solid #fff;display:flex;align-items:center;justify-content:center}
.side-arrow{position:absolute;top:1075px;width:26px;height:26px;border-radius:50%;display:flex;align-items:center;justify-content:center}

/* about */
.about-bg{left:0;top:1360px;width:1200px;height:459px;background:var(--light)}
.about-text{left:560px;top:1502px;width:530px;font-size:15px;line-height:30px;color:#3a3a3a}
.btn-grey{position:absolute;left:560px;top:1697px;width:166px;height:52px;border-radius:26px;background:var(--grey-btn);color:#fff;font-family:'Montserrat',sans-serif;font-weight:700;font-size:16px;display:flex;align-items:center;justify-content:center}

/* testimonials */
.dot{position:absolute;border-radius:50%}
.quote{position:absolute;font-family:Georgia,serif;font-size:150px;color:#e4e4e4;line-height:1}

/* gallery */
.tile{position:absolute;border-radius:4px}

/* contact */
.info-icon{position:absolute;left:100px;width:50px;height:50px;border-radius:50%;border:1.5px solid #ccc;display:flex;align-items:center;justify-content:center}
.info-title{position:absolute;left:163px;font-family:'Montserrat',sans-serif;font-weight:700;font-size:19px;color:var(--ink)}
.info-text{position:absolute;left:163px;font-size:15px;line-height:25px;color:#333}
.field{position:absolute;background:#f9f9f9;box-shadow:0 6px 14px rgba(0,0,0,.06);font-size:15px;color:#888;padding:18px 0 0 24px}

/* footer */
.footer{left:0;top:3763px;width:1200px;height:401px;background:var(--footer)}
.f-head{position:absolute;top:76px;font-family:'Montserrat',sans-serif;font-weight:700;font-size:17px;color:#fff}
.f-link{position:absolute;left:112px;font-size:15px;color:#fff}
.f-text{position:absolute;font-size:15px;line-height:26px;color:#fff}
</style>
</head>
<body>

<!-- header -->
<header class="abs topbar">
  <div class="icon-circle" style="left:115px;top:30px;width:40px;height:40px;background:var(--yellow)">
    <svg width="18" height="18" viewBox="0 0 24 24" fill="#fff"><path d="M6.6 10.8a15.1 15.1 0 0 0 6.6 6.6l2.2-2.2a1 1 0 0 1 1-.25 11.4 11.4 0 0 0 3.6.57 1 1 0 0 1 1 1V20a1 1 0 0 1-1 1A17 17 0 0 1 3 4a1 1 0 0 1 1-1h3.5a1 1 0 0 1 1 1c0 1.25.2 2.45.57 3.57a1 1 0 0 1-.25 1z"/></svg>
  </div>
  <div class="abs contact-label" style="left:165px;top:28px">CALL US</div>
  <div class="abs contact-value" style="left:165px;top:46px;font-weight:700">+1 202 555 0147</div>

  <div class="brand">Brimsett Gardening</div>

  <div class="icon-circle" style="left:804px;top:32px;width:42px;height:42px;background:var(--yellow)">
    <svg width="18" height="18" viewBox="0 0 24 24" fill="#fff"><path d="M2 5h20v14H2z"/><path d="M2 5l10 8 10-8" stroke="#f7d12a" stroke-width="2" fill="none"/></svg>
  </div>
  <div class="abs contact-label" style="left:859px;top:30px">EMAIL</div>
  <div class="abs contact-value" style="left:859px;top:52px">info@brimsettgardening.com</div>
</header>

<nav class="abs navbar">
  <div class="nav-home">Home</div>
  <div class="nav-item" style="left:228px">Services</div>
  <div class="nav-item" style="left:319px">About Us</div>
  <div class="nav-item" style="left:414px">Contact Us</div>
  <div class="nav-item" style="left:522px">Showcase</div>
  <div class="search">Search
    <svg class="abs" style="right:14px;top:10px" width="15" height="15" viewBox="0 0 24 24" fill="none" stroke="#111" stroke-width="3"><circle cx="10" cy="10" r="7"/><path d="M15 15l6 6"/></svg>
  </div>
</nav>

<!-- hero -->
<section class="abs hero" role="img" aria-label="Landscaped garden with lawn, flower beds and a house in the background">
  <div class="abs hero-shade"></div>
  <div class="abs hero-kicker">WELCOME TO</div>
  <h1 class="abs hero-title">BRIMSETT<br>GARDENING</h1>
  <p class="abs hero-text">Lorem ipsum dolor sit amet, consectetur adipiscing elit, sed do eiusmod tempor</p>
  <div class="btn-yellow" style="left:112px;top:369px;width:167px;height:52px;font-size:16px">GET STARTED</div>
</section>

<!-- services -->
<h2 class="heading section-title" style="top:822px">Our Services</h2>

<div class="side-arrow" style="left:41px;background:var(--yellow)">
  <svg width="10" height="10" viewBox="0 0 10 10"><path d="M6.5 1.5L3 5l3.5 3.5" stroke="#111" stroke-width="1.5" fill="none"/></svg>
</div>
<div class="side-arrow" style="left:1131px;background:#eeeeee">
  <svg width="10" height="10" viewBox="0 0 10 10"><path d="M3.5 1.5L7 5 3.5 8.5" stroke="#aaa" stroke-width="1.5" fill="none"/></svg>
</div>

<div class="card" style="left:110px">
  <div class="card-img" role="img" aria-label="Worker laying turf beside a paved path" style="background:linear-gradient(160deg,#9a8f84,#6e6a5c 50%,#4a5a34)"></div>
  <div class="card-shade"></div>
  <div class="card-title">Landscaping</div>
  <div class="card-text">Lorem ipsum dolor sit amet, consectetur adipiscing elit,</div>
  <div class="card-arrow"><svg width="16" height="16" viewBox="0 0 16 16"><path d="M2 8h11M9 4l4 4-4 4" stroke="#111" stroke-width="2" fill="none"/></svg></div>
</div>
<div class="card" style="left:442px">
  <div class="card-img" role="img" aria-label="Workers pouring a concrete slab in a garden" style="background:linear-gradient(160deg,#7e9a6a,#5e6a6a 45%,#2a3e55)"></div>
  <div class="card-shade"></div>
  <div class="card-title">Concreting</div>
  <div class="card-text">Lorem ipsum dolor sit amet, consectetur adipiscing elit,</div>
  <div class="card-arrow"><svg width="16" height="16" viewBox="0 0 16 16"><path d="M2 8h11M9 4l4 4-4 4" stroke="#111" stroke-width="2" fill="none"/></svg></div>
</div>
<div class="card" style="left:774px">
  <div class="card-img" role="img" aria-label="Curved stone retaining wall with flower bed" style="background:linear-gradient(160deg,#5f8a3c,#a08a6a 45%,#6a5a44)"></div>
  <div class="card-shade"></div>
  <div class="card-title">Retaining walls</div>
  <div class="card-text">Lorem ipsum dolor sit amet, consectetur adipiscing elit,</div>
  <div class="card-arrow"><svg width="16" height="16" viewBox="0 0 16 16"><path d="M2 8h11M9 4l4 4-4 4" stroke="#111" stroke-width="2" fill="none"/></svg></div>
</div>

<!-- about -->
<div class="abs about-bg"></div>
<svg class="abs" style="left:0;top:1360px" width="1200" height="459" viewBox="0 0 1200 459">
  <path d="M420 459 C 430 220 560 20 760 0 L1200 0 L1200 459 Z" fill="#f7d12a"/>
</svg>
<div class="abs" role="img" aria-label="Cobblestone garden path lined with potted flowers" style="left:-40px;top:1420px;width:562px;height:402px;border-radius:0 50% 50% 0 / 0 50% 50% 0;background:radial-gradient(ellipse at 50% 40%,#8a9a6a,#3c5228 55%,#1e2c14)"></div>
<h2 class="abs heading" style="left:563px;top:1440px;font-size:34px">About Brimsett Gardening</h2>
<p class="abs about-text">Lorem ipsum dolor sit amet, consectetur adipiscing elit, sed do eiusmod tempor incididunt ut labore et dolore magna aliqua. Quis ipsum suspendisse ultrices gravida. Risus commodo viverra maecenas accumsan lacus vel facilisis. Lorem ipsum dolor sit amet, consectetur adipiscing elit, sed do eiusmod tempor incididunt ut labore et dolore magna aliqua. Quis ipsum suspendisse ultrices gravida.</p>
<div class="btn-grey">LEARN MORE</div>

<!-- testimonials -->
<h2 class="heading section-title" style="top:1978px">Client Testimonials</h2>
<div class="dot" style="left:907px;top:1990px;width:10px;height:10px;background:#f39a1e"></div>
<div class="dot" style="left:137px;top:2036px;width:7px;height:7px;background:#2aa8e0"></div>
<div class="dot" style="left:324px;top:2141px;width:10px;height:10px;background:#f2c418"></div>
<div class="dot" style="left:815px;top:2168px;width:10px;height:10px;background:#9b3bd6"></div>
<div class="dot" style="left:1015px;top:2337px;width:10px;height:10px;background:#1ed3a0"></div>

<div class="abs" role="img" aria-label="Client portrait" style="left:135px;top:2119px;width:48px;height:48px;border-radius:50%;background:#9aa6b0"></div>
<div class="abs" role="img" aria-label="Client portrait" style="left:950px;top:2038px;width:50px;height:50px;border-radius:50%;background:#9a8f88"></div>
<div class="abs" role="img" aria-label="Client portrait" style="left:552px;top:2060px;width:90px;height:90px;border-radius:50%;background:#b8b0a8"></div>

<div class="icon-circle" style="left:207px;top:2171px;width:32px;height:32px;background:#ececec">
  <svg width="10" height="10" viewBox="0 0 10 10"><path d="M6.5 1.5L3 5l3.5 3.5" stroke="#999" stroke-width="1.5" fill="none"/></svg>
</div>
<div class="icon-circle" style="left:961px;top:2171px;width:32px;height:32px;background:var(--yellow)">
  <svg width="10" height="10" viewBox="0 0 10 10"><path d="M3.5 1.5L7 5 3.5 8.5" stroke="#111" stroke-width="1.5" fill="none"/></svg>
</div>

<div class="abs" style="left:0;width:1200px;top:2166px;text-align:center;font-family:'Montserrat',sans-serif;font-weight:600;font-size:20px;color:#111">Marlow Everett</div>
<div class="abs" style="left:0;width:1200px;top:2194px;text-align:center;font-size:15px;color:#333">Lorem Ipsum</div>
<div class="abs" style="left:0;width:1200px;top:2222px;text-align:center;font-size:19px;letter-spacing:3px;color:#f7b31a">★★★★★</div>
<div class="quote" style="left:245px;top:2190px">“</div>
<div class="quote" style="left:880px;top:2330px">”</div>
<p class="abs" style="left:280px;top:2266px;width:640px;text-align:center;font-size:15px;line-height:26px;color:#888">Lorem ipsum dolor sit amet, consectetur adipiscing elit, sed do eiusmod tempor incididunt ut labore et dolore magna aliqua. Quis ipsum suspendisse ultrices gravida. Risus commodo viverra maecenas accumsan lacus vel facilisis.</p>

<!-- gallery -->
<h2 class="heading section-title" style="top:2503px">Project Gallery</h2>
<div class="tile" role="img" aria-label="Curved paver path across a green lawn" style="left:118px;top:2592px;width:427px;height:351px;background:linear-gradient(170deg,#6a7a5a,#5f9a2a 40%,#8a8a80 75%,#6a7a4a)"></div>
<div class="tile" role="img" aria-label="Lawn leading to a house between pink flower beds" style="left:559px;top:2592px;width:254px;height:247px;background:linear-gradient(180deg,#3a4a34,#4c7a2a 55%,#6aa030)"></div>
<div class="tile" role="img" aria-label="Sunlit lawn edge with flowering shrubs" style="left:827px;top:2592px;width:255px;height:247px;background:radial-gradient(circle at 80% 10%,#f4e8b0,#9a8a4a 30%,#5a7a2a 70%)"></div>
<div class="tile" role="img" aria-label="Stone garden path through colourful flowers" style="left:118px;top:2956px;width:254px;height:247px;background:linear-gradient(170deg,#6a8a5a,#6a6aa0 45%,#8a7a6a)"></div>
<div class="tile" role="img" aria-label="Stone garden steps with planting" style="left:385px;top:2956px;width:254px;height:247px;background:linear-gradient(170deg,#5a7a3a,#a89a7a 55%,#7a6a52)"></div>
<div class="tile" role="img" aria-label="Aerial view of a garden pergola" style="left:653px;top:2852px;width:429px;height:353px;background:radial-gradient(ellipse at 50% 40%,#3a3c34,#262a22 60%,#1a2014)"></div>
<svg class="abs" style="left:852px;top:2948px" width="40" height="40" viewBox="0 0 40 40" fill="none" stroke="#fff" stroke-width="3"><circle cx="16" cy="16" r="12"/><path d="M25 25l11 11M16 10v12M10 16h12"/></svg>

<!-- contact -->
<h2 class="heading section-title" style="top:3312px">Contact Us</h2>
<div class="info-icon" style="top:3400px"><svg width="18" height="18" viewBox="0 0 24 24" fill="none" stroke="#f2c418" stroke-width="2"><path d="M12 22s7-7 7-12a7 7 0 0 0-14 0c0 5 7 12 7 12z"/><circle cx="12" cy="10" r="2.5"/></svg></div>
<div class="info-title" style="top:3396px">LOCATION</div>
<div class="info-text" style="top:3424px;width:230px">27/c Brimsett Gardening sit amet, consectetur adipiscing</div>
<div class="info-icon" style="top:3508px"><svg width="17" height="17" viewBox="0 0 24 24" fill="#f2c418"><path d="M6.6 10.8a15.1 15.1 0 0 0 6.6 6.6l2.2-2.2a1 1 0 0 1 1-.25 11.4 11.4 0 0 0 3.6.57 1 1 0 0 1 1 1V20a1 1 0 0 1-1 1A17 17 0 0 1 3 4a1 1 0 0 1 1-1h3.5a1 1 0 0 1 1 1c0 1.25.2 2.45.57 3.57a1 1 0 0 1-.25 1z"/></svg></div>
<div class="info-title" style="top:3508px">PHONE</div>
<div class="info-text" style="top:3535px">+1 202 555 0147</div>
<div class="info-icon" style="top:3597px"><svg width="17" height="17" viewBox="0 0 24 24" fill="#f2c418"><path d="M2 5h20v14H2z"/><path d="M2 5l10 8 10-8" stroke="#fff" stroke-width="2" fill="none"/></svg></div>
<div class="info-title" style="top:3597px">EMAIL</div>
<div class="info-text" style="top:3625px">info@brimsettgardening.com</div>

<div class="field" style="left:422px;top:3396px;width:317px;height:52px">Name</div>
<div class="field" style="left:422px;top:3464px;width:317px;height:52px">Phone</div>
<div class="field" style="left:422px;top:3532px;width:317px;height:52px">Email</div>
<div class="abs" style="left:421px;top:3601px;width:318px;height:52px;background:var(--yellow);display:flex;align-items:center;justify-content:center;font-family:'Montserrat',sans-serif;font-weight:700;font-size:15px;color:#111">SUBMIT</div>
<div class="field" style="left:760px;top:3396px;width:317px;height:257px;background:#fff;box-shadow:0 6px 20px rgba(0,0,0,.08)">Type your message</div>

<!-- footer -->
<footer class="abs footer">
  <div class="f-head" style="left:110px">QUICK LINK</div>
  <div class="f-link" style="top:118px">Home</div>
  <div class="f-link" style="top:148px">Services</div>
  <div class="f-link" style="top:178px">About Us</div>
  <div class="f-link" style="top:208px">Contact Us</div>
  <div class="f-link" style="top:238px">Showcase</div>

  <div class="f-head" style="left:254px">SUBSCRIBE TO OUR NEWSLETTER</div>
  <div class="f-text" style="left:257px;top:112px;width:300px">Lorem ipsum dolor sit amet, consectetur adipiscing elit, sed do</div>
  <div class="abs" style="left:256px;top:175px;width:273px;height:42px;border:1.5px solid #ddd;border-radius:22px;padding:11px 0 0 20px;font-size:15px;color:#ccc">Enter Your Email
    <div class="icon-circle" style="right:4px;top:4px;width:32px;height:32px;background:var(--yellow)">
      <svg width="14" height="14" viewBox="0 0 24 24" fill="#111"><path d="M2 12l20-9-7 19-3-8z"/></svg>
    </div>
  </div>

  <div class="f-head" style="left:597px;top:78px">CONTACT US</div>
  <svg class="abs" style="left:598px;top:120px" width="14" height="14" viewBox="0 0 24 24" fill="#fff"><path d="M12 22s7-7 7-12a7 7 0 0 0-14 0c0 5 7 12 7 12z"/></svg>
  <div class="f-text" style="left:625px;top:112px;width:250px">27/c Brimsett Gardening sit amet, consectetur adipiscing</div>
  <svg class="abs" style="left:598px;top:172px" width="14" height="14" viewBox="0 0 24 24" fill="#fff"><path d="M2 5h20v14H2z"/></svg>
  <div class="f-text" style="left:625px;top:165px">info@brimsettgardening.com</div>
  <svg class="abs" style="left:598px;top:206px" width="14" height="14" viewBox="0 0 24 24" fill="#fff"><path d="M6.6 10.8a15.1 15.1 0 0 0 6.6 6.6l2.2-2.2a1 1 0 0 1 1-.25 11.4 11.4 0 0 0 3.6.57 1 1 0 0 1 1 1V20a1 1 0 0 1-1 1A17 17 0 0 1 3 4a1 1 0 0 1 1-1h3.5a1 1 0 0 1 1 1c0 1.25.2 2.45.57 3.57a1 1 0 0 1-.25 1z"/></svg>
  <div class="f-text" style="left:625px;top:199px">+1 202 555 0147</div>

  <div class="abs" style="left:862px;top:150px;width:240px;text-align:center;font-family:'Montserrat',sans-serif;font-weight:600;font-size:22px;letter-spacing:4px;line-height:34px;color:var(--yellow-deep)">BRIMSETT<br>GARDENING</div>

  <div class="abs" style="left:110px;top:309px;width:980px;height:1px;background:#333"></div>
  <div class="abs" style="left:0;width:1200px;top:347px;text-align:center;font-size:15px;color:#fff">©Copyrights 2024 &nbsp; Brimsett Gardening &nbsp; | &nbsp; All Rights Reserved</div>
</footer>

</body>
</html>
```